Business Card Design Project - del varosi group

dear Sirs

we need business card design for our group ( DEL Varosi Group ) , i have got the Logo design of our group from pixel harbor in previous , so all need details relating to our group i think available with you, as well as the the chosen logo design

we hope to provide us with business card logo that to be appropaite and satisfactory to us .

thanks

note : logo design of our group is attached .
Updates

Reason: please extend the deadline of my project for additional 15 days because i didn't received appropriate design for our gruop yet . kindly beaware that i have received 77 design till now , supossed to send me 200-250 design at least . thanks

Target Market(s)

contents

name : Kerem EL Nadiri

position : Operation Manager

Industry/Entity Type

Business

Requirements
Must have

• person name

group logo
Nice to have
• logo color matching with back background

```html
<!DOCTYPE html>
<html lang="en">
<head>
<meta charset="utf-8">
<title>DEL Varosi Group — Business Cards</title>
<link href="https://fonts.googleapis.com/css2?family=Open+Sans:wght@400;600;700&display=swap" rel="stylesheet">
<style>
  :root {
    --board: #b0862b;
    --card: #ffffff;
    --blue-deep: #0b4a88;
    --blue-mid: #1a72b8;
    --brand-blue: #114f8e;
    --gold: #d6b25c;
    --ink: #1b1b1b;
    --icon-blue: #1f6fb5;
  }
  * { box-sizing: border-box; margin: 0; padding: 0; }
  html, body {
    width: 1200px; height: 686px; overflow: hidden;
    background: var(--board);
    font-family: "Open Sans", Arial, sans-serif;
  }
  .board { position: relative; width: 1200px; height: 686px; }

  .card {
    position: absolute; width: 482px; height: 276px;
    background: var(--card); border-radius: 21px; overflow: hidden;
    box-shadow: 2px 3px 6px rgba(0,0,0,.35);
  }
  .card--front { left: 86px; top: 51px; }
  .card--back  { left: 620px; top: 52px; }
  .card--alt   { left: 344px; top: 364px; }

  .brand {
    position: absolute; left: 0; right: 0;
    display: flex; align-items: center; justify-content: center; gap: 10px;
    color: var(--brand-blue); font-weight: 600; font-size: 31px;
    letter-spacing: .5px; white-space: nowrap;
  }
  .brand__square { width: 24px; height: 24px; background: var(--brand-blue); }
  .card--front .brand { top: 60px; }
  .card--back .brand  { top: 98px; }
  .card--alt .brand   { top: 114px; }

  .band {
    position: absolute; left: 0; right: 0;
    background: linear-gradient(90deg, var(--blue-deep) 0%, var(--blue-mid) 55%, var(--blue-deep) 100%);
  }
  .rule { position: absolute; left: 0; right: 0; height: 4px; background: var(--gold); }

  .card--front .band { top: 149px; height: 29px; display: flex; align-items: center; justify-content: center; color: #fff; }
  .card--front .rule { top: 179px; }
  .person__name { font-weight: 700; font-size: 15px; }
  .person__divider { width: 1px; height: 14px; background: #fff; margin: 0 9px; }
  .person__role { font-weight: 600; font-size: 12px; }

  .contact {
    position: absolute; left: 0; right: 0; top: 202px;
    display: flex; flex-direction: column; align-items: center; gap: 3px;
    font-size: 12.5px; color: var(--ink);
  }
  .contact__row { display: flex; gap: 16px; align-items: center; }
  .contact__item { display: flex; align-items: center; gap: 2px; }
  .contact__item svg { width: 11px; height: 11px; fill: var(--icon-blue); }

  .card--back .rule { top: 220px; }
  .card--back .band { top: 225px; height: 28px; }

  .card--alt .band--top { top: 0; height: 54px; }
  .card--alt .rule--top { top: 54px; }
  .card--alt .rule--bottom { top: 214px; }
  .card--alt .band--bottom { top: 219px; height: 57px; }

  .web {
    position: absolute; left: 0; right: 0; text-align: center;
    color: #fff; font-weight: 700; font-size: 11px; letter-spacing: 1.5px;
  }
  .card--back .web { top: 231px; }
  .card--alt .web { top: 241px; }
</style>
</head>
<body>
<main class="board">

  <section class="card card--front" aria-label="Business card front">
    <div class="brand"><span class="brand__square"></span>DEL VAROSI GROUP</div>
    <div class="band">
      <span class="person__name">Kerem EL Nadiri</span>
      <span class="person__divider"></span>
      <span class="person__role">Operation Manager</span>
    </div>
    <div class="rule"></div>
    <div class="contact">
      <div class="contact__row">
        <span class="contact__item"><svg viewBox="0 0 24 24"><path d="M6.6 10.8a15 15 0 0 0 6.6 6.6l2.2-2.2c.3-.3.7-.4 1-.2 1.1.4 2.3.6 3.6.6.6 0 1 .4 1 1V20c0 .6-.4 1-1 1A17 17 0 0 1 3 4c0-.6.4-1 1-1h3.5c.6 0 1 .4 1 1 0 1.3.2 2.5.6 3.6.1.3 0 .7-.2 1z"/></svg>(TF)123-456-7890</span>
        <span class="contact__item"><svg viewBox="0 0 24 24"><path d="M6.6 10.8a15 15 0 0 0 6.6 6.6l2.2-2.2c.3-.3.7-.4 1-.2 1.1.4 2.3.6 3.6.6.6 0 1 .4 1 1V20c0 .6-.4 1-1 1A17 17 0 0 1 3 4c0-.6.4-1 1-1h3.5c.6 0 1 .4 1 1 0 1.3.2 2.5.6 3.6.1.3 0 .7-.2 1z"/></svg>123-456-7890</span>
        <span class="contact__item"><svg viewBox="0 0 24 24"><path d="M6 2h10v6H6zM3 9h18v9h-3v4H6v-4H3zm5 7v4h8v-4z"/></svg>123-456-7890</span>
      </div>
      <div class="contact__row">
        <span class="contact__item"><svg viewBox="0 0 24 24"><path d="M2 5h20v14H2zm2 2v.5l8 5 8-5V7z"/></svg>name@website.com</span>
        <span class="contact__item"><svg viewBox="0 0 24 24"><path d="M12 2a10 10 0 1 0 0 20 10 10 0 0 0 0-20zm6.9 9h-3a15 15 0 0 0-1.3-6A8 8 0 0 1 18.9 11zM12 4.1c.9 1.2 1.7 3.7 1.9 6.9h-3.8c.2-3.2 1-5.7 1.9-6.9zM9.4 5a15 15 0 0 0-1.3 6h-3A8 8 0 0 1 9.4 5zM5.1 13h3a15 15 0 0 0 1.3 6A8 8 0 0 1 5.1 13zm6.9 6.9c-.9-1.2-1.7-3.7-1.9-6.9h3.8c-.2 3.2-1 5.7-1.9 6.9zm2.6-.9a15 15 0 0 0 1.3-6h3a8 8 0 0 1-4.3 6z"/></svg>www.website.com</span>
      </div>
      <div class="contact__row"><span>Street name City, State, zip code</span></div>
    </div>
  </section>

  <section class="card card--back" aria-label="Business card back">
    <div class="brand"><span class="brand__square"></span>DEL VAROSI GROUP</div>
    <div class="rule"></div>
    <div class="band"></div>
    <p class="web">www.website.com</p>
  </section>

  <section class="card card--alt" aria-label="Business card back, alternative">
    <div class="band band--top"></div>
    <div class="rule rule--top"></div>
    <div class="brand"><span class="brand__square"></span>DEL VAROSI GROUP</div>
    <div class="rule rule--bottom"></div>
    <div class="band band--bottom"></div>
    <p class="web">www.website.com</p>
  </section>

</main>
</body>
</html>
```